Website needed for modern mobile app developer for small business'

Hi

We are looking for someone to design a very modern looking website with company logo that outlines what our business is and let's users purchase a mobile app designed by our company. (For ideas think quillnest.example or ) The user should be able to describe what functionality they require and we will go and provide a test version of their app built

We would also like a testimonials page.

I currently have hosting on Brindle Hosting, so if this could be taken into account that would be great.
Updates

here is the logo - if colour scheme could match that would be great Added Wednesday, March 30, 2016

Target Market(s)

Small and medium business

Industry/Entity Type

Business

Number of Pages Required

3 page

Requirements
Must have
• Homepage who we are and what we offer
• Pricing page explaining the different products available - HTML5 app, Robo App or Pocket app with an option to purchase
• A testimonials page
• A one that makes it easier for potential customers to get in contact.

```html
<!DOCTYPE html>
<html lang="en">
<head>
<meta charset="utf-8">
<title>Loftwave – Mobile Apps for Small Business</title>
<link href="https://fonts.googleapis.com/css2?family=Questrial&family=Arimo:wght@400;700&display=swap" rel="stylesheet">
<style>
  :root {
    --brand: #0b4f8f;
    --brand-dark: #083f75;
    --hero-a: #0a6fb0;
    --hero-b: #0a4d8c;
    --ink: #1d1d1d;
    --muted: #6b6b6b;
    --card-bg: #f6fafd;
    --card-line: #d6e4ef;
    --soft-bg: #f3f8fc;
    --contact-bg: #f3f3f3;
    --footer-bg: #232323;
    --footer-text: #a7a7a7;
    --white: #ffffff;
  }
  * { box-sizing: border-box; margin: 0; padding: 0; }
  html, body { width: 742px; height: 1200px; overflow: hidden; }
  body { font-family: "Arimo", Arial, sans-serif; color: var(--ink); background: var(--white); position: relative; }
  .heading { font-family: "Questrial", sans-serif; font-weight: 400; }

  .site-header { position: absolute; top: 0; left: 0; width: 742px; height: 47px; background: var(--white); }
  .brand { position: absolute; left: 82px; top: 5px; font-family: "Questrial", sans-serif; font-size: 29px; color: var(--brand); }
  .main-nav { position: absolute; right: 82px; top: 18px; display: flex; gap: 20px; font-size: 7.5px; }
  .main-nav a { color: var(--muted); text-decoration: none; }
  .main-nav a.active { color: var(--brand); }

  .hero { position: absolute; top: 47px; left: 0; width: 742px; height: 332px; }
  .hero-photo { position: absolute; inset: 0; background: linear-gradient(100deg, var(--hero-a) 0%, #1a7fc0 30%, var(--hero-b) 62%, #083f7e 100%); }
  .hero-col { position: absolute; top: 104px; width: 230px; color: var(--white); }
  .hero-col h2 { font-size: 22px; margin-bottom: 8px; }
  .hero-col p { font-size: 6.6px; line-height: 12px; opacity: .92; }
  .btn-light { display: inline-block; margin-top: 9px; background: var(--white); color: var(--brand); font-size: 6.5px; padding: 5px 8px; text-decoration: none; }
  .hero-dots { position: absolute; left: 345px; top: 311px; display: flex; gap: 10px; }
  .hero-dots span { width: 5px; height: 5px; border-radius: 50%; background: var(--white); }
  .hero-dots span.current { background: transparent; border: 1px solid var(--white); }

  .pricing { position: absolute; top: 379px; left: 0; width: 742px; height: 379px; }
  .section-title { position: absolute; left: 0; width: 742px; text-align: center; font-size: 22px; color: var(--ink); }
  .pricing .section-title { top: 38px; }
  .pricing-intro { position: absolute; top: 78px; left: 82px; width: 577px; text-align: center; font-size: 6.8px; line-height: 13px; color: var(--muted); }
  .plan { position: absolute; top: 130px; width: 177px; height: 205px; background: var(--card-bg); border: 1px solid var(--card-line); text-align: center; }
  .plan-icon { position: absolute; left: 72px; top: 20px; width: 32px; height: 36px; border-radius: 4px; }
  .plan h3 { position: absolute; top: 71px; width: 100%; font-size: 16px; color: var(--brand); }
  .plan ul { position: absolute; top: 99px; width: 100%; list-style: none; font-size: 6.3px; color: var(--muted); line-height: 14.7px; }
  .btn-buy { position: absolute; left: 50px; top: 161px; width: 77px; height: 27px; line-height: 27px; background: var(--brand); color: var(--white); font-size: 7.5px; text-decoration: none; border-radius: 2px; }

  .testimonials { position: absolute; top: 758px; left: 0; width: 742px; height: 298px; background: var(--soft-bg); }
  .testimonials .section-title { top: 44px; }
  .avatar { position: absolute; border-radius: 50%; }
  .avatar.side { width: 42px; height: 42px; top: 88px; background: radial-gradient(circle at 50% 40%, #7fb8e6, #2f7fc4); }
  .avatar.main { width: 60px; height: 60px; top: 80px; left: 341px; background: radial-gradient(circle at 50% 40%, #d8d8d8, #5d5d5d); border: 2px solid var(--white); }
  .quote-box { position: absolute; left: 154px; top: 157px; width: 434px; height: 93px; background: var(--white); border: 1px solid #dde3e8; }
  .quote-box::before { content: ""; position: absolute; left: 210px; top: -6px; width: 10px; height: 10px; background: var(--white); border-left: 1px solid #dde3e8; border-top: 1px solid #dde3e8; transform: rotate(45deg); }
  .quote-mark { position: absolute; left: 13px; top: 8px; font-family: Georgia, serif; font-size: 26px; color: #9a9a9a; }
  .quote-text { position: absolute; left: 44px; top: 12px; width: 370px; font-size: 9.5px; line-height: 17px; color: #8a8a8a; }
  .quote-author { position: absolute; left: 44px; top: 66px; font-size: 12px; color: var(--ink); }
  .quote-author small { font-size: 7.5px; }
  .slider-arrow { position: absolute; top: 194px; }

  .quick-contact { position: absolute; top: 1056px; left: 0; width: 742px; height: 83px; background: var(--contact-bg); }
  .quick-contact .section-title { top: 12px; font-size: 17px; }
  .contact-form { position: absolute; left: 82px; top: 42px; width: 577px; height: 24px; }
  .field { position: absolute; top: 0; height: 24px; background: var(--white); border: 1px solid #dcdcdc; font-size: 7px; color: var(--muted); padding: 8px 10px; }
  .btn-submit { position: absolute; top: 0; left: 528px; width: 49px; height: 24px; background: #3a3a3a; color: var(--white); font-size: 8px; text-align: center; line-height: 24px; }

  .site-footer { position: absolute; top: 1139px; left: 0; width: 742px; height: 61px; background: var(--footer-bg); }
  .footer-nav { position: absolute; left: 82px; top: 18px; font-size: 6.5px; color: var(--footer-text); }
  .footer-nav span { margin: 0 4px; color: #666; }
  .copyright { position: absolute; left: 82px; top: 35px; font-size: 6.5px; color: var(--footer-text); }
  .social { position: absolute; left: 585px; top: 24px; display: flex; gap: 4px; }
  .social span { width: 16px; height: 16px; border-radius: 50%; }
</style>
</head>
<body>
  <header class="site-header">
    <div class="brand">Loftwave</div>
    <nav class="main-nav">
      <a class="active" href="#">Home</a><a href="#">Pricing</a><a href="#">Testimonials</a><a href="#">Contact us</a>
    </nav>
  </header>

  <section class="hero">
    <div class="hero-photo" role="img" aria-label="Blue-toned photo of a hand holding a smartphone"></div>
    <div class="hero-col" style="left:114px">
      <h2 class="heading">Who we are</h2>
      <p>Donec faucibus tellus at eros pellentesque, eu imperdiet turpis lobortis. Donec dignissim ipsum vehicula sapien mattis, ut laoreet dui rutrum. Morbi in enim enim. Morbi sagittis ultricies viverra. Curabitur consectetur libero ut tortor imperdiet, vel varius mauris pellentesque.</p>
      <a class="btn-light" href="#">Read More</a>
    </div>
    <div class="hero-col" style="left:403px">
      <h2 class="heading">What we do</h2>
      <p>Donec faucibus tellus at eros pellentesque, eu imperdiet turpis lobortis. Donec dignissim ipsum vehicula sapien mattis, ut laoreet dui rutrum. Morbi in enim enim. Morbi sagittis ultricies viverra. Curabitur consectetur libero ut tortor imperdiet, vel varius mauris pellentesque.</p>
      <a class="btn-light" href="#">Read More</a>
    </div>
    <div class="hero-dots"><span class="current"></span><span></span><span></span><span></span></div>
  </section>

  <section class="pricing">
    <h2 class="section-title heading">Pricing</h2>
    <p class="pricing-intro">Cras volutpat id justo cursus consequat. Donec faucibus tellus at eros pellentesque, eu imperdiet turpis lobortis. Donec dignissim ipsum vehicula sapien mattis, ut laoreet dui rutrum. Morbi in enim enim. Morbi sagittis ultricies viverra. Curabitur consectetur libero ut tortor imperdiet, vel varius mauris pellentesque. Mauris lacinia, neque eget mollis pharetra, ipsum elit ullamcorper purus, a hendrerit ipsum massa vel nisl. Maecenas sit amet dolor non arcu efficitur sodales ut in nisl. Donec sit amet condimentum felis, nec ultrices massa.</p>

    <article class="plan" style="left:82px">
      <div class="plan-icon" style="background:#e44d26"></div>
      <h3 class="heading">HTML5</h3>
      <ul><li>Donec congue gravida diam vel porta</li><li>Cras cursus purus a tortor sollicitudin dignissim</li><li>Pellentesque vitae accumsan velit</li><li>Aenean bibendum bibendum orci, non lacinia nisl</li></ul>
      <a class="btn-buy" href="#">Purchase Now</a>
    </article>
    <article class="plan" style="left:282px">
      <div class="plan-icon" style="background:#8bc34a;border-radius:50%"></div>
      <h3 class="heading">Robo Apps</h3>
      <ul><li>Donec congue gravida diam vel porta</li><li>Cras cursus purus a tortor sollicitudin dignissim</li><li>Pellentesque vitae accumsan velit</li><li>Aenean bibendum bibendum orci, non lacinia nisl</li></ul>
      <a class="btn-buy" href="#">Purchase Now</a>
    </article>
    <article class="plan" style="left:482px">
      <div class="plan-icon" style="background:#1a1a1a;border-radius:50%"></div>
      <h3 class="heading">Pocket Apps</h3>
      <ul><li>Donec congue gravida diam vel porta</li><li>Cras cursus purus a tortor sollicitudin dignissim</li><li>Pellentesque vitae accumsan velit</li><li>Aenean bibendum bibendum orci, non lacinia nisl</li></ul>
      <a class="btn-buy" href="#">Purchase Now</a>
    </article>
  </section>

  <section class="testimonials">
    <h2 class="section-title heading">Testimonials</h2>
    <div class="avatar side" style="left:296px" role="img" aria-label="Client portrait"></div>
    <div class="avatar main" role="img" aria-label="Client portrait"></div>
    <div class="avatar side" style="left:404px" role="img" aria-label="Client portrait"></div>
    <blockquote class="quote-box">
      <span class="quote-mark">&ldquo;</span>
      <p class="quote-text">Donec neque augue, scelerisque sed aliquet eget, malesuada quis velit. Mauris at aliquam leo. Proin eu nulla vel sapien tristique ornare non et tellus. Duis vel felis nibh.</p>
      <p class="quote-author">Owen Marsh., <small>Company name</small></p>
    </blockquote>
    <svg class="slider-arrow" style="left:82px" width="10" height="16" viewBox="0 0 10 16"><path d="M8 1 L2 8 L8 15" fill="none" stroke="#b5bec6" stroke-width="1.5"/></svg>
    <svg class="slider-arrow" style="left:650px" width="10" height="16" viewBox="0 0 10 16"><path d="M2 1 L8 8 L2 15" fill="none" stroke="#b5bec6" stroke-width="1.5"/></svg>
  </section>

  <section class="quick-contact">
    <h2 class="section-title heading">Quick Contact</h2>
    <form class="contact-form">
      <div class="field" style="left:0;width:105px">Name</div>
      <div class="field" style="left:109px;width:105px">Email</div>
      <div class="field" style="left:217px;width:105px">Company</div>
      <div class="field" style="left:327px;width:196px">Message</div>
      <div class="btn-submit">SUBMIT</div>
    </form>
  </section>

  <footer class="site-footer">
    <div class="footer-nav">Home<span>|</span>Pricing<span>|</span>Testimonials<span>|</span>Contact us</div>
    <div class="copyright">Copyright &copy; 2016 &nbsp;Loftwave. &nbsp;All rights reserved.</div>
    <div class="social" aria-label="Social links">
      <span style="background:#3b5998"></span><span style="background:#1da1f2"></span><span style="background:#d62b2b"></span><span style="background:#4a86b8"></span>
    </div>
  </footer>
</body>
</html>
```